New business card for a regional office of a US M&A company

We need business card for a finance company, office based in Hong Kong , our Head office is in US, our business is to Merge and acquires companies , the new office will be a regional office for the Asia Pacific region. We want to use the head office logo as attached ( but don't have to be exactly the same, can be a variation to it) as a base and then add Asia Pacific alongside the logo.
We would prefer to have be bilingual Eng + Chinese, although we don't really have Chinese company name .

Industry/Entity Type

Business

Contact Information for Business Card

Clara Jo Tsang
 

VP,
APAC M&A Operations
Orin Vantage Asia Pacific Limited
 
Unit 1407, K18
18 Tai Lok Shan Road, 
Hong Kong 
 
M: +852 6038 1742
T : +852 2836 4100
F : +852 2836 4177
VOIP: 4158
 
cjtsang@orinvantage.com

Font styles to use
Serif
Sans Serif

Colors

Designer to choose colors to be used in the design.

Requirements
Must have
• APAC Office

```html
<!DOCTYPE html>
<html lang="en">
<head>
<meta charset="utf-8">
<title>Orin Vantage – Business Card</title>
<link rel="stylesheet" href="https://fonts.googleapis.com/css2?family=Fjalla+One&family=Open+Sans:wght@400;600;700&display=swap">
<style>
  :root {
    --backdrop: #1c1c1d;
    --card: #262627;
    --card-edge: #303031;
    --accent: #29aed0;
    --ink: #f2f2f2;
    --silver: #b9b9bb;
  }
  * { box-sizing: border-box; margin: 0; padding: 0; }
  html, body {
    width: 1200px;
    height: 900px;
    overflow: hidden;
    background: var(--backdrop);
    font-family: "Open Sans", Arial, sans-serif;
  }
  .canvas {
    width: 1200px;
    height: 900px;
    display: flex;
    flex-direction: column;
    align-items: center;
    justify-content: center;
    gap: 36px;
  }
  .card {
    width: 660px;
    height: 380px;
    background: var(--card);
    border: 1px solid var(--card-edge);
    position: relative;
  }
  /* Front */
  .card-front {
    display: flex;
    align-items: center;
    justify-content: center;
    gap: 18px;
  }
  .brand-mark {
    width: 34px;
    height: 34px;
    background: var(--silver);
  }
  .brand-name {
    font-family: "Open Sans", Arial, sans-serif;
    font-weight: 700;
    font-size: 40px;
    letter-spacing: 3px;
    color: var(--silver);
  }
  /* Back */
  .identity {
    position: absolute;
    left: 60px;
    top: 118px;
    width: 250px;
    text-align: right;
  }
  .person-name {
    font-family: "Fjalla One", "Arial Narrow", sans-serif;
    font-size: 36px;
    line-height: 1;
    color: var(--accent);
    text-transform: uppercase;
    letter-spacing: 0.5px;
  }
  .person-title {
    margin-top: 8px;
    font-size: 17px;
    line-height: 1.2;
    color: var(--ink);
    letter-spacing: 0.5px;
  }
  .divider {
    position: absolute;
    left: 330px;
    top: 118px;
    width: 2px;
    height: 84px;
    background: var(--accent);
  }
  .contact-list {
    position: absolute;
    left: 352px;
    top: 114px;
    list-style: none;
  }
  .contact-list li {
    display: flex;
    align-items: center;
    gap: 14px;
    font-size: 16px;
    line-height: 22px;
    color: var(--ink);
    letter-spacing: 1px;
  }
  .contact-list svg {
    width: 13px;
    height: 13px;
    flex: none;
  }
  .address {
    position: absolute;
    left: 60px;
    bottom: 58px;
    font-size: 17px;
    color: var(--ink);
    letter-spacing: 0.3px;
  }
</style>
</head>
<body>
<main class="canvas">
  <section class="card card-front">
    <div class="brand-mark"></div>
    <div class="brand-name">ORIN VANTAGE</div>
  </section>

  <section class="card card-back">
    <div class="identity">
      <h1 class="person-name">Clara Jo Tsang</h1>
      <p class="person-title">VP,<br>APAC M&amp;A Operations</p>
    </div>
    <div class="divider"></div>
    <ul class="contact-list">
      <li>
        <svg viewBox="0 0 14 14" aria-hidden="true"><rect x="3.5" y="1" width="7" height="12" rx="1.2" fill="none" stroke="var(--accent)" stroke-width="1.4"/></svg>
        +852 6038 1742
      </li>
      <li>
        <svg viewBox="0 0 14 14" aria-hidden="true"><path d="M3 1.5 L5.5 1.5 L6.5 4.5 L5 5.8 C5.8 7.6 6.6 8.5 8.3 9.2 L9.6 7.6 L12.5 8.6 L12.5 11.2 C12.5 12 11.8 12.6 11 12.5 C6 12 2 8 1.5 3 C1.4 2.2 2.1 1.5 3 1.5 Z" fill="var(--accent)"/></svg>
        +852 2836 4100
      </li>
      <li>
        <svg viewBox="0 0 14 14" aria-hidden="true"><rect x="4" y="1" width="6" height="4" fill="var(--accent)"/><rect x="1" y="5" width="12" height="5" rx="1" fill="var(--accent)"/><rect x="4" y="9" width="6" height="4" fill="var(--accent)"/></svg>
        +852 2836 4177
      </li>
      <li>
        <svg viewBox="0 0 14 14" aria-hidden="true"><rect x="1" y="3" width="12" height="8.5" fill="var(--accent)"/><path d="M1 3 L7 8 L13 3" fill="none" stroke="var(--card)" stroke-width="1.2"/></svg>
        cjtsang@orinvantage.com
      </li>
    </ul>
    <p class="address">Unit 1407, K18 18 Tai Lok Shan Road, Hong Kong</p>
  </section>
</main>
</body>
</html>
```